Brenvik Systems PowerPoint Template

Project Title: Professional & Functional PowerPoint Template (.potx) – Brenvik Systems Rebrand

Project Overview:
Brenvik Systems has recently undergone a complete rebranding, including a new logo, website, and visual identity. We need a professional, high-end PowerPoint Template (.potx) that reflects our new look while being highly functional for everyday use.

We previously had a design created, but it was built incorrectly (static images, oversized file, no Master Slides). The goal of this project is to take our new aesthetic and build a "workable" template where layouts are controlled by Master Slides and text is easily editable.

Style & Brand Direction:
The template must be an extension of our new website: https://www.brenvik-systems.example/

Aesthetic: Modern, clean, high-tech, and "Industrial Tech."

Color Palette: Please pull the primary blues, greys, and accent colors directly from the website.

Imagery/Graphics: Use clean lines and subtle tech-inspired gradients. Avoid "clutter."

Tone: Innovative, precise, and professional.

Technical Requirements (Crucial)
Format: Must be delivered as a PowerPoint Template file (** .potx **).

Functionality: All layouts must be built using Slide Masters. Users should be able to click "New Slide" and choose from specific layouts.

Native Elements: Do NOT use full-page background images for text areas. Bullet points must use native PowerPoint list functionality (not individual text boxes).

File Size: The template must be optimized and lightweight.

Fonts: Use standard professional fonts or provide the specific web-safe equivalent used on our site (e.g., Montserrat, Open Sans, etc.).

Required Slide Layouts
Please include a minimum of 10–12 Master layouts, including:
*Title Slide (2-3 variations: Dark and Light)
*Agenda/Table of Contents
*Section Header/Divider Slides
*Standard Text/Bullet Slide
*Two-Column Text Slide
*Image + Text Layouts (Left/Right variations)
*Data/Chart Slide (Styled bar/pie charts that match the brand)
*Process/Timeline Slide (Infographic style)
*Section slide

Attachments Provided
Brand Assets (.zip): Contains our new logo in various formats.

Inspiration/Existing PPT: We have attached the previous design created by our web agency. Note: Use this for visual inspiration ONLY. Do not copy the file structure, as it is technically flawed.

Deliverables
Final .potx file.

All used icons or custom graphics in vector format (if applicable).

Instruction note on any specific fonts used.

Target Market(s)

Internal communication and external (investors, customers)

Industry/Entity Type

Semiconductor, Automotive

Requirements
Must have
• A potx file

```html
<!DOCTYPE html>
<html lang="en">
<head>
<meta charset="utf-8">
<title>Brenvik Systems – Presentation Template Overview</title>
<link rel="stylesheet" href="https://fonts.googleapis.com/css2?family=Poppins:wght@400;500;600;700&family=Montserrat:wght@300;400;500&display=swap">
<style>
:root{
  --canvas:#a9a9a9;
  --blue:#1d3fe3;
  --blue-deep:#0e2aa8;
  --navy:#0a1a7a;
  --ink:#0b0f1e;
  --dark:#0a0e1c;
  --grey-text:#555b66;
  --light:#f1f2f4;
  --rule:#2b4be6;
  --white:#ffffff;
  --periwinkle:#9aa8f5;
}
*{margin:0;padding:0;box-sizing:border-box}
html,body{width:1031px;height:1200px;overflow:hidden;background:var(--canvas)}
body{position:relative;font-family:"Poppins",sans-serif;color:var(--ink)}
.slide{position:absolute;width:482px;height:271px;transform:scale(.5795);transform-origin:0 0;overflow:hidden;background:var(--white)}
.abs{position:absolute}
.fill{position:absolute;inset:0}
.title-xl{position:absolute;left:35px;top:22px;font-size:29px;font-weight:600;line-height:34px;color:var(--white)}
.confidential{position:absolute;left:34px;top:173px;font-size:10px;font-weight:600;line-height:10px;color:var(--white)}
.wordmark{position:absolute;left:34px;top:205px;display:flex;align-items:center;gap:9px}
.wordmark .mark{width:32px;height:32px;background:var(--blue)}
.wordmark .name{font-size:36px;font-weight:700;letter-spacing:.5px;color:var(--white);line-height:40px}
.heading{position:absolute;left:20px;top:16px;font-size:16px;font-weight:600;color:var(--ink)}
.sub{position:absolute;left:20px;top:42px;font-size:10px;font-weight:500;color:var(--ink)}
.copy{font-size:6.3px;line-height:8.1px;text-align:justify;color:var(--ink)}
.copy p+p{margin-top:6px}
.col{position:absolute;top:42px;width:212px}
.footer{position:absolute;left:20px;right:20px;top:246px;height:1px;background:var(--rule)}
.footer::after{content:"";position:absolute;right:0;top:-5px;width:10px;height:10px;border:1px solid var(--rule);background:var(--white)}
.on-dark .heading,.on-dark .copy{color:var(--white)}
.on-dark .footer{background:#4a63ff}
.on-dark .footer::after{background:transparent;border-color:#c9d2ff}
.toc-item{position:absolute;width:200px;height:34px;border-bottom:1px dashed #9aa0aa}
.toc-item b{display:block;font-size:7.5px;font-weight:600;color:var(--blue)}
.toc-item span{display:block;font-size:6.3px;font-weight:500;margin-top:2px}
.toc-item i{position:absolute;right:6px;top:8px;font-style:normal;font-size:6.5px;font-weight:600}
.check{position:absolute;font-size:7.5px;font-weight:500;display:flex;align-items:center;gap:3px}
.check svg{width:8px;height:8px}
.centre-title{position:absolute;left:0;right:0;text-align:center;font-size:29px;font-weight:600;line-height:34px}
.centre-mark{position:absolute;left:225px;width:32px;height:32px}
.process-title{position:absolute;left:0;right:0;top:22px;text-align:center;font-family:"Montserrat",sans-serif;font-size:17px;font-weight:400;color:#6b6f78;letter-spacing:.5px}
.process-title small{font-size:4.5px;letter-spacing:2.4px;vertical-align:6px;margin-left:2px}
.step-label{position:absolute;width:70px;text-align:center}
.step-label b{display:block;font-size:4.5px;font-weight:600;color:var(--blue-deep)}
.step-label span{display:block;font-size:3.2px;line-height:4px;color:#9aa0aa;margin-top:3px}
</style>
</head>
<body>

<!-- Row 1: title variations -->
<section class="slide" style="left:72px;top:59px;background:var(--dark)">
  <div class="fill" role="img" aria-label="Photo of a precision inspection lens above a silicon wafer, dark tones" style="background:radial-gradient(ellipse 60% 80% at 72% 45%,#5a5f68 0%,#24282f 35%,transparent 60%),linear-gradient(160deg,#1a2230 0%,#0b1220 55%,#2a3a48 100%)"></div>
  <h1 class="title-xl">Enlightened<br>Engineering</h1>
  <div class="confidential">Confidential<br>and Proprietary</div>
  <div class="wordmark"><span class="mark"></span><span class="name">BRENVIK</span></div>
</section>

<section class="slide" style="left:375px;top:59px">
  <div class="abs" role="img" aria-label="Photo of a precision inspection lens on a white background" style="left:250px;top:0;width:232px;height:271px;background:radial-gradient(ellipse 45% 70% at 55% 35%,#4d5157 0%,#2a2c30 45%,transparent 70%),radial-gradient(ellipse 60% 12% at 60% 100%,#dfe6f2 0%,transparent 100%)"></div>
  <h1 class="title-xl" style="color:var(--ink)">Enlightened<br><span style="color:var(--blue)">Engineering</span></h1>
  <div class="confidential" style="color:var(--ink)">Confidential<br>and Proprietary</div>
  <div class="wordmark"><span class="mark"></span><span class="name" style="color:var(--ink)">BRENVIK</span></div>
</section>

<section class="slide" style="left:679px;top:59px;background:var(--navy)">
  <div class="fill" role="img" aria-label="Photo of an inspection lens in front of a blue-lit server room" style="background:radial-gradient(ellipse 45% 75% at 62% 38%,#45484e 0%,#1f2126 40%,transparent 65%),linear-gradient(135deg,#0a1660 0%,#0e23a0 55%,#0b1a78 100%)"></div>
  <h1 class="title-xl">Enlightened<br>Engineering</h1>
  <div class="confidential">Confidential<br>and Proprietary</div>
  <div class="wordmark"><span class="mark" style="background:var(--white)"></span><span class="name">BRENVIK</span></div>
</section>

<!-- Row 2 -->
<section class="slide" style="left:72px;top:244px">
  <h2 class="abs" style="left:26px;top:26px;font-size:21px;font-weight:600;line-height:23px">Table of<br><span style="color:var(--blue)">Contents</span></h2>
  <div class="abs" style="left:147px;top:26px;width:50px;height:50px;background:var(--blue)"></div>
  <div class="abs" style="left:200px;top:26px;width:282px;height:50px;background:var(--light);padding:14px 12px 0;font-size:5.6px;font-weight:600;line-height:7.5px">Here You Can Add Some Brief Text To Explain The Title This Is Just a Demo So Consider Replacing This Text with Your Own Presentation Content. It Is Highly Recommended That You Replace This Demo Text</div>
  <div class="toc-item" style="left:25px;top:98px"><b>Welcome Slide</b><span>Write a Short Summary for this Slide</span><i>01</i></div>
  <div class="toc-item" style="left:25px;top:136px"><b>About Us</b><span>Write a Short Summary for this Slide</span><i>02</i></div>
  <div class="toc-item" style="left:25px;top:173px"><b>Mission &amp; Vision</b><span>Write a Short Summary for this Slide</span><i>03</i></div>
  <div class="toc-item" style="left:25px;top:211px"><b>Our History</b><span>Write a Short Summary for this Slide</span><i>04</i></div>
  <div class="toc-item" style="left:256px;top:98px"><b>Pricing Slide</b><span>Write a Short Summary for this Slide</span><i>05</i></div>
  <div class="toc-item" style="left:256px;top:136px"><b>Our Infographics</b><span>Write a Short Summary for this Slide</span><i>06</i></div>
  <div class="toc-item" style="left:256px;top:173px"><b>Client Reviews</b><span>Write a Short Summary for this Slide</span><i>07</i></div>
  <div class="toc-item" style="left:256px;top:211px"><b>Data &amp; Charts</b><span>Write a Short Summary for this Slide</span><i>08</i></div>
</section>

<section class="slide" style="left:375px;top:244px;background:var(--blue)">
  <div class="fill" role="img" aria-label="Photo of a silicon wafer under a probe, tinted blue" style="background:radial-gradient(ellipse 55% 50% at 45% 58%,#3a5bff 0%,#1f3fe0 45%,#0e2098 100%)"></div>
  <span class="centre-mark" style="top:75px;background:var(--white)"></span>
  <h2 class="centre-title" style="top:128px;color:var(--white)">Enlightened<br>Engineering</h2>
</section>

<section class="slide" style="left:679px;top:244px">
  <h2 class="heading">Heading Goes Here</h2>
  <div class="copy abs" style="left:20px;top:42px;width:442px">
    <p>Lorem ipsum dolor sit amet, consectetuer adipiscing elit, sed diam nonummy nibh euismod tincidunt ut laoreet dolore magna aliquam erat volutpat. Ut wisi enim ad minim veniam, quis nostrud exerci tation ullamcorper suscipit lobortis nisl ut aliquip ex ea commodo consequat. Duis autem vel eum iriure dolor in hendrerit in vulputate velit esse molestie consequat, vel illum dolore eu feugiat nulla facilisis at vero eros et accumsan et iusto odio dignissim qui blandit praesent luptatum zzril delenit augue duis dolore te feugait nulla facilisi.</p>
    <p>Lorem ipsum dolor sit amet, cons ectetuer adipiscing elit, sed diam nonummy nibh euismod tincidunt ut laoreet dolore magna aliquam erat volutpat. Ut wisi enim ad minim veniam, quis nostrud exerci tation ullamcorper suscipit lobortis nisl ut aliquip ex ea commodo consequat.</p>
  </div>
  <h2 class="heading" style="top:125px">Heading Goes Here</h2>
  <svg width="0" height="0" style="position:absolute"><defs><symbol id="tick" viewBox="0 0 10 10"><circle cx="5" cy="5" r="4.3" fill="none" stroke="#1d3fe3" stroke-width="1"/><path d="M3 5.2l1.5 1.5L7.2 3.8" fill="none" stroke="#1d3fe3" stroke-width="1"/></symbol></defs></svg>
  <div class="check" style="left:20px;top:154px"><svg><use href="#tick"/></svg>Lorem ipsum dolor sit amet</div>
  <div class="check" style="left:20px;top:172px"><svg><use href="#tick"/></svg>Lorem ipsum dolor sit amet</div>
  <div class="check" style="left:20px;top:190px"><svg><use href="#tick"/></svg>Lorem ipsum dolor sit amet</div>
  <div class="check" style="left:20px;top:208px"><svg><use href="#tick"/></svg>Lorem ipsum dolor sit amet</div>
  <div class="check" style="left:182px;top:154px"><svg><use href="#tick"/></svg>Lorem ipsum dolor sit amet</div>
  <div class="check" style="left:182px;top:172px"><svg><use href="#tick"/></svg>Lorem ipsum dolor sit amet</div>
  <div class="check" style="left:182px;top:190px"><svg><use href="#tick"/></svg>Lorem ipsum dolor sit amet</div>
  <div class="check" style="left:182px;top:208px"><svg><use href="#tick"/></svg>Lorem ipsum dolor sit amet</div>
  <div class="check" style="left:344px;top:154px"><svg><use href="#tick"/></svg>Lorem ipsum dolor sit amet</div>
  <div class="check" style="left:344px;top:172px"><svg><use href="#tick"/></svg>Lorem ipsum dolor sit amet</div>
  <div class="check" style="left:344px;top:190px"><svg><use href="#tick"/></svg>Lorem ipsum dolor sit amet</div>
  <div class="check" style="left:344px;top:208px"><svg><use href="#tick"/></svg>Lorem ipsum dolor sit amet</div>
  <div class="footer"></div>
</section>

<!-- Row 3: two-column text -->
<section class="slide" style="left:72px;top:430px">
  <h2 class="heading">Heading Goes Here</h2>
  <div class="col copy" style="left:20px"><p>Lorem ipsum dolor sit amet, consectetuer adipiscing elit, sed diam nonummy nibh euismod tincidunt ut laoreet dolore magna aliquam erat volutpat. Ut wisi enim ad minim veniam, quis nostrud exerci tation ullamcorper suscipit lobortis nisl ut aliquip ex ea commodo consequat. Duis autem vel eum iriure dolor in hendrerit in vulputate velit esse molestie consequat, vel illum dolore eu feugiat nulla facilisis at vero eros et accumsan et iusto odio dignissim qui blandit praesent luptatum zzril delenit augue duis dolore te feugait nulla facilisi.</p><p>Lorem ipsum dolor sit amet, cons ectetuer adipiscing elit, sed diam nonummy nibh euismod tincidunt ut laoreet dolore magna aliquam erat volutpat. Ut wisi enim ad minim veniam, quis nostrud exerci tation ullamcorper suscipit lobortis nisl ut aliquip ex ea commodo consequat.</p><p>Lorem ipsum dolor sit amet, cons ectetuer adipiscing elit, sed diam nonummy nibh euismod tincidunt ut laoreet dolore magna aliquam erat volutpat. Ut wisi enim ad minim veniam, quis nostrud exerci tation ullamcorper suscipit lobortis nisl ut aliquip ex ea commodo consequat.</p></div>
  <div class="col copy" style="left:250px"><p>Lorem ipsum dolor sit amet, consectetuer adipiscing elit, sed diam nonummy nibh euismod tincidunt ut laoreet dolore magna aliquam erat volutpat. Ut wisi enim ad minim veniam, quis nostrud exerci tation ullamcorper suscipit lobortis nisl ut aliquip ex ea commodo consequat. Duis autem vel eum iriure dolor in hendrerit in vulputate velit esse molestie consequat, vel illum dolore eu feugiat nulla facilisis at vero eros et accumsan et iusto odio dignissim qui blandit praesent luptatum zzril delenit augue duis dolore te feugait nulla facilisi.</p><p>Lorem ipsum dolor sit amet, cons ectetuer adipiscing elit, sed diam nonummy nibh euismod tincidunt ut laoreet dolore magna aliquam erat volutpat. Ut wisi enim ad minim veniam, quis nostrud exerci tation ullamcorper suscipit lobortis nisl ut aliquip ex ea commodo consequat.</p><p>Lorem ipsum dolor sit amet, cons ectetuer adipiscing elit, sed diam nonummy nibh euismod tincidunt ut laoreet dolore magna aliquam erat volutpat. Ut wisi enim ad minim veniam, quis nostrud exerci tation ullamcorper suscipit lobortis nisl ut aliquip ex ea commodo consequat.</p></div>
  <div class="footer"></div>
</section>

<section class="slide on-dark" style="left:375px;top:430px;background:var(--blue-deep)">
  <div class="fill" role="img" aria-label="Faint blue-tinted photo of a wafer inspection scene" style="background:linear-gradient(135deg,#1330c4 0%,#0f2aa8 50%,#1a3be0 100%)"></div>
  <h2 class="heading">Heading Goes Here</h2>
  <div class="col copy" style="left:20px"><p>Lorem ipsum dolor sit amet, consectetuer adipiscing elit, sed diam nonummy nibh euismod tincidunt ut laoreet dolore magna aliquam erat volutpat. Ut wisi enim ad minim veniam, quis nostrud exerci tation ullamcorper suscipit lobortis nisl ut aliquip ex ea commodo consequat. Duis autem vel eum iriure dolor in hendrerit in vulputate velit esse molestie consequat, vel illum dolore eu feugiat nulla facilisis at vero eros et accumsan et iusto odio dignissim qui blandit praesent luptatum zzril delenit augue duis dolore te feugait nulla facilisi.</p><p>Lorem ipsum dolor sit amet, cons ectetuer adipiscing elit, sed diam nonummy nibh euismod tincidunt ut laoreet dolore magna aliquam erat volutpat. Ut wisi enim ad minim veniam, quis nostrud exerci tation ullamcorper suscipit lobortis nisl ut aliquip ex ea commodo consequat.</p><p>Lorem ipsum dolor sit amet, cons ectetuer adipiscing elit, sed diam nonummy nibh euismod tincidunt ut laoreet dolore magna aliquam erat volutpat. Ut wisi enim ad minim veniam, quis nostrud exerci tation ullamcorper suscipit lobortis nisl ut aliquip ex ea commodo consequat.</p></div>
  <div class="col copy" style="left:250px"><p>Lorem ipsum dolor sit amet, consectetuer adipiscing elit, sed diam nonummy nibh euismod tincidunt ut laoreet dolore magna aliquam erat volutpat. Ut wisi enim ad minim veniam, quis nostrud exerci tation ullamcorper suscipit lobortis nisl ut aliquip ex ea commodo consequat. Duis autem vel eum iriure dolor in hendrerit in vulputate velit esse molestie consequat, vel illum dolore eu feugiat nulla facilisis at vero eros et accumsan et iusto odio dignissim qui blandit praesent luptatum zzril delenit augue duis dolore te feugait nulla facilisi.</p><p>Lorem ipsum dolor sit amet, cons ectetuer adipiscing elit, sed diam nonummy nibh euismod tincidunt ut laoreet dolore magna aliquam erat volutpat. Ut wisi enim ad minim veniam, quis nostrud exerci tation ullamcorper suscipit lobortis nisl ut aliquip ex ea commodo consequat.</p><p>Lorem ipsum dolor sit amet, cons ectetuer adipiscing elit, sed diam nonummy nibh euismod tincidunt ut laoreet dolore magna aliquam erat volutpat. Ut wisi enim ad minim veniam, quis nostrud exerci tation ullamcorper suscipit lobortis nisl ut aliquip ex ea commodo consequat.</p></div>
  <div class="footer"></div>
</section>

<section class="slide on-dark" style="left:679px;top:430px;background:var(--dark)">
  <div class="fill" role="img" aria-label="Dark photo of semiconductor equipment" style="background:radial-gradient(ellipse 50% 60% at 50% 40%,#2a2e36 0%,#121520 55%,#05070d 100%)"></div>
  <h2 class="heading" style="color:var(--blue)">Heading Goes Here</h2>
  <div class="col copy" style="left:20px"><p>Lorem ipsum dolor sit amet, consectetuer adipiscing elit, sed diam nonummy nibh euismod tincidunt ut laoreet dolore magna aliquam erat volutpat. Ut wisi enim ad minim veniam, quis nostrud exerci tation ullamcorper suscipit lobortis nisl ut aliquip ex ea commodo consequat. Duis autem vel eum iriure dolor in hendrerit in vulputate velit esse molestie consequat, vel illum dolore eu feugiat nulla facilisis at vero eros et accumsan et iusto odio dignissim qui blandit praesent luptatum zzril delenit augue duis dolore te feugait nulla facilisi.</p><p>Lorem ipsum dolor sit amet, cons ectetuer adipiscing elit, sed diam nonummy nibh euismod tincidunt ut laoreet dolore magna aliquam erat volutpat. Ut wisi enim ad minim veniam, quis nostrud exerci tation ullamcorper suscipit lobortis nisl ut aliquip ex ea commodo consequat.</p><p>Lorem ipsum dolor sit amet, cons ectetuer adipiscing elit, sed diam nonummy nibh euismod tincidunt ut laoreet dolore magna aliquam erat volutpat. Ut wisi enim ad minim veniam, quis nostrud exerci tation ullamcorper suscipit lobortis nisl ut aliquip ex ea commodo consequat.</p></div>
  <div class="col copy" style="left:250px"><p>Lorem ipsum dolor sit amet, consectetuer adipiscing elit, sed diam nonummy nibh euismod tincidunt ut laoreet dolore magna aliquam erat volutpat. Ut wisi enim ad minim veniam, quis nostrud exerci tation ullamcorper suscipit lobortis nisl ut aliquip ex ea commodo consequat. Duis autem vel eum iriure dolor in hendrerit in vulputate velit esse molestie consequat, vel illum dolore eu feugiat nulla facilisis at vero eros et accumsan et iusto odio dignissim qui blandit praesent luptatum zzril delenit augue duis dolore te feugait nulla facilisi.</p><p>Lorem ipsum dolor sit amet, cons ectetuer adipiscing elit, sed diam nonummy nibh euismod tincidunt ut laoreet dolore magna aliquam erat volutpat. Ut wisi enim ad minim veniam, quis nostrud exerci tation ullamcorper suscipit lobortis nisl ut aliquip ex ea commodo consequat.</p><p>Lorem ipsum dolor sit amet, cons ectetuer adipiscing elit, sed diam nonummy nibh euismod tincidunt ut laoreet dolore magna aliquam erat volutpat. Ut wisi enim ad minim veniam, quis nostrud exerci tation ullamcorper suscipit lobortis nisl ut aliquip ex ea commodo consequat.</p></div>
  <div class="footer"></div>
</section>

<!-- Row 4: image + text, line chart -->
<section class="slide" style="left:72px;top:616px">
  <h2 class="heading">Heading Goes Here</h2>
  <div class="col copy" style="left:20px"><p>Lorem ipsum dolor sit amet, consectetuer adipiscing elit, sed diam nonummy nibh euismod tincidunt ut laoreet dolore magna aliquam erat volutpat. Ut wisi enim ad minim veniam, quis nostrud exerci tation ullamcorper suscipit lobortis nisl ut aliquip ex ea commodo consequat. Duis autem vel eum iriure dolor in hendrerit in vulputate velit esse molestie consequat, vel illum dolore eu feugiat nulla facilisis at vero eros et accumsan et iusto odio dignissim qui blandit praesent luptatum zzril delenit augue duis dolore te feugait nulla facilisi.</p><p>Lorem ipsum dolor sit amet, cons ectetuer adipiscing elit, sed diam nonummy nibh euismod tincidunt ut laoreet dolore magna aliquam erat volutpat. Ut wisi enim ad minim veniam, quis nostrud exerci tation ullamcorper suscipit lobortis nisl ut aliquip ex ea commodo consequat.</p><p>Lorem ipsum dolor sit amet, cons ectetuer adipiscing elit, sed diam nonummy nibh euismod tincidunt ut laoreet dolore magna aliquam erat volutpat. Ut wisi enim ad minim veniam, quis nostrud exerci tation ullamcorper suscipit lobortis nisl ut aliquip ex ea commodo consequat.</p></div>
  <div class="abs" role="img" aria-label="Photo of a probe needle over a colourful wafer die grid" style="left:250px;top:44px;width:212px;height:179px;background:radial-gradient(ellipse 70% 40% at 45% 95%,#7a4a8a 0%,#3a2a50 40%,transparent 70%),linear-gradient(180deg,#2a2c31 0%,#15171c 60%,#1d1a26 100%)"></div>
  <div class="footer"></div>
</section>

<section class="slide" style="left:375px;top:616px">
  <h2 class="heading">Heading Goes Here</h2>
  <div class="abs" role="img" aria-label="Photo of a probe needle over a colourful wafer die grid" style="left:20px;top:44px;width:212px;height:179px;background:radial-gradient(ellipse 70% 40% at 45% 95%,#7a4a8a 0%,#3a2a50 40%,transparent 70%),linear-gradient(180deg,#2a2c31 0%,#15171c 60%,#1d1a26 100%)"></div>
  <div class="col copy" style="left:250px"><p>Lorem ipsum dolor sit amet, consectetuer adipiscing elit, sed diam nonummy nibh euismod tincidunt ut laoreet dolore magna aliquam erat volutpat. Ut wisi enim ad minim veniam, quis nostrud exerci tation ullamcorper suscipit lobortis nisl ut aliquip ex ea commodo consequat. Duis autem vel eum iriure dolor in hendrerit in vulputate velit esse molestie consequat, vel illum dolore eu feugiat nulla facilisis at vero eros et accumsan et iusto odio dignissim qui blandit praesent luptatum zzril delenit augue duis dolore te feugait nulla facilisi.</p><p>Lorem ipsum dolor sit amet, cons ectetuer adipiscing elit, sed diam nonummy nibh euismod tincidunt ut laoreet dolore magna aliquam erat volutpat. Ut wisi enim ad minim veniam, quis nostrud exerci tation ullamcorper suscipit lobortis nisl ut aliquip ex ea commodo consequat.</p><p>Lorem ipsum dolor sit amet, cons ectetuer adipiscing elit, sed diam nonummy nibh euismod tincidunt ut laoreet dolore magna aliquam erat volutpat. Ut wisi enim ad minim veniam, quis nostrud exerci tation ullamcorper suscipit lobortis nisl ut aliquip ex ea commodo consequat.</p></div>
  <div class="footer"></div>
</section>

<section class="slide" style="left:679px;top:616px">
  <h2 class="heading">Heading Goes Here</h2>
  <div class="sub">Line Chart</div>
  <svg class="abs" style="left:0;top:0" width="482" height="271" viewBox="0 0 482 271" font-family="Poppins, sans-serif">
    <g stroke="#e3e5ea" stroke-width=".5">
      <line x1="30" y1="76" x2="462" y2="76"/><line x1="30" y1="90.7" x2="462" y2="90.7"/><line x1="30" y1="105.4" x2="462" y2="105.4"/><line x1="30" y1="120.1" x2="462" y2="120.1"/><line x1="30" y1="134.8" x2="462" y2="134.8"/><line x1="30" y1="149.5" x2="462" y2="149.5"/><line x1="30" y1="164.2" x2="462" y2="164.2"/><line x1="30" y1="178.9" x2="462" y2="178.9"/><line x1="30" y1="193.6" x2="462" y2="193.6"/><line x1="30" y1="208.3" x2="462" y2="208.3"/><line x1="30" y1="223" x2="462" y2="223"/>
      <line x1="48" y1="76" x2="48" y2="223"/><line x1="84" y1="76" x2="84" y2="223"/><line x1="120" y1="76" x2="120" y2="223"/><line x1="156" y1="76" x2="156" y2="223"/><line x1="192" y1="76" x2="192" y2="223"/><line x1="228" y1="76" x2="228" y2="223"/><line x1="264" y1="76" x2="264" y2="223"/><line x1="300" y1="76" x2="300" y2="223"/><line x1="336" y1="76" x2="336" y2="223"/><line x1="372" y1="76" x2="372" y2="223"/><line x1="408" y1="76" x2="408" y2="223"/><line x1="444" y1="76" x2="444" y2="223"/>
    </g>
    <g font-size="3.5" fill="#333" text-anchor="end">
      <text x="27" y="77">100</text><text x="27" y="92">90</text><text x="27" y="106">80</text><text x="27" y="121">70</text><text x="27" y="136">60</text><text x="27" y="150">50</text><text x="27" y="165">40</text><text x="27" y="180">30</text><text x="27" y="194">20</text><text x="27" y="209">10</text><text x="27" y="224">0</text>
    </g>
    <g font-size="3.2" fill="#333" text-anchor="middle">
      <text x="48" y="232">JAN</text><text x="84" y="232">FEB</text><text x="120" y="232">MAR</text><text x="156" y="232">APR</text><text x="192" y="232">MAY</text><text x="228" y="232">JUN</text><text x="264" y="232">JUL</text><text x="300" y="232">AUG</text><text x="336" y="232">SEP</text><text x="372" y="232">OCT</text><text x="408" y="232">NOV</text><text x="444" y="232">DEC</text>
    </g>
    <polyline fill="none" stroke="#8a8e96" stroke-width=".8" points="30,208 66,179 102,193 138,149 174,135 210,164 246,149 282,164 318,134 354,105 390,120 426,135 462,105"/>
    <polyline fill="none" stroke="#1d3fe3" stroke-width=".9" points="30,164 66,149 102,164 138,120 174,120 210,135 246,120 282,120 318,90.7 354,84 390,84 426,90.7 462,84"/>
    <g fill="#8a8e96"><circle cx="30" cy="208" r="1.2"/><circle cx="66" cy="179" r="1.2"/><circle cx="102" cy="193" r="1.2"/><circle cx="138" cy="149" r="1.2"/><circle cx="174" cy="135" r="1.2"/><circle cx="210" cy="164" r="1.2"/><circle cx="246" cy="149" r="1.2"/><circle cx="282" cy="164" r="1.2"/><circle cx="318" cy="134" r="1.2"/><circle cx="354" cy="105" r="1.2"/><circle cx="390" cy="120" r="1.2"/><circle cx="426" cy="135" r="1.2"/><circle cx="462" cy="105" r="1.2"/></g>
    <g fill="#1d3fe3"><circle cx="30" cy="164" r="1.2"/><circle cx="66" cy="149" r="1.2"/><circle cx="102" cy="164" r="1.2"/><circle cx="138" cy="120" r="1.2"/><circle cx="174" cy="120" r="1.2"/><circle cx="210" cy="135" r="1.2"/><circle cx="246" cy="120" r="1.2"/><circle cx="282" cy="120" r="1.2"/><circle cx="318" cy="90.7" r="1.2"/><circle cx="354" cy="84" r="1.2"/><circle cx="390" cy="84" r="1.2"/><circle cx="426" cy="90.7" r="1.2"/><circle cx="462" cy="84" r="1.2"/></g>
    <circle cx="413" cy="67" r="2" fill="#8a8e96"/><text x="417" y="68.5" font-size="4" fill="#333">Sales</text>
    <circle cx="436" cy="67" r="2" fill="#1d3fe3"/><text x="440" y="68.5" font-size="4" fill="#333">Orders</text>
  </svg>
  <div class="footer"></div>
</section>

<!-- Row 5: stacked chart and process -->
<section class="slide" style="left:72px;top:802px">
  <h2 class="heading">Heading Goes Here</h2>
  <div class="sub" style="left:18px">Stacked Chart</div>
  <svg class="abs" style="left:0;top:0" width="482" height="271" viewBox="0 0 482 271" font-family="Poppins, sans-serif">
    <line x1="18" y1="61" x2="464" y2="61" stroke="#d8dbe2" stroke-width=".5"/>
    <g stroke="#e3e5ea" stroke-width=".5">
      <line x1="30" y1="78" x2="462" y2="78"/><line x1="30" y1="92.7" x2="462" y2="92.7"/><line x1="30" y1="107.4" x2="462" y2="107.4"/><line x1="30" y1="122.1" x2="462" y2="122.1"/><line x1="30" y1="136.8" x2="462" y2="136.8"/><line x1="30" y1="151.5" x2="462" y2="151.5"/><line x1="30" y1="166.2" x2="462" y2="166.2"/><line x1="30" y1="180.9" x2="462" y2="180.9"/><line x1="30" y1="195.6" x2="462" y2="195.6"/><line x1="30" y1="210.3" x2="462" y2="210.3"/><line x1="30" y1="225" x2="462" y2="225"/>
    </g>
    <g font-size="3.5" fill="#333" text-anchor="end">
      <text x="27" y="79">100</text><text x="27" y="94">90</text><text x="27" y="108">80</text><text x="27" y="123">70</text><text x="27" y="138">60</text><text x="27" y="152">50</text><text x="27" y="167">40</text><text x="27" y="182">30</text><text x="27" y="196">20</text><text x="27" y="211">10</text><text x="27" y="226">0</text>
    </g>
    <g id="bars">
      <!-- each bar: receipts (bottom), orders (middle), sales (top) -->
      <rect x="36" y="210.3" width="12" height="14.7" fill="#9aa8f5"/><rect x="36" y="195.6" width="12" height="14.7" fill="#0a1a7a"/><rect x="36" y="180.9" width="12" height="14.7" fill="#1d3fe3"/>
      <rect x="72" y="180.9" width="12" height="44.1" fill="#9aa8f5"/><rect x="72" y="151.5" width="12" height="29.4" fill="#0a1a7a"/><rect x="72" y="92.7" width="12" height="58.8" fill="#1d3fe3"/>
      <rect x="108" y="210.3" width="12" height="14.7" fill="#9aa8f5"/><rect x="108" y="195.6" width="12" height="14.7" fill="#0a1a7a"/><rect x="108" y="136.8" width="12" height="58.8" fill="#1d3fe3"/>
      <rect x="144" y="199" width="12" height="26" fill="#9aa8f5"/><rect x="144" y="99" width="12" height="100" fill="#0a1a7a"/><rect x="144" y="78" width="12" height="21" fill="#1d3fe3"/>
      <rect x="180" y="166.2" width="12" height="58.8" fill="#9aa8f5"/><rect x="180" y="136.8" width="12" height="29.4" fill="#0a1a7a"/><rect x="180" y="107.4" width="12" height="29.4" fill="#1d3fe3"/>
      <rect x="216" y="210.3" width="12" height="14.7" fill="#9aa8f5"/><rect x="216" y="195.6" width="12" height="14.7" fill="#0a1a7a"/>
      <rect x="252" y="195.6" width="12" height="29.4" fill="#9aa8f5"/><rect x="252" y="166.2" width="12" height="29.4" fill="#0a1a7a"/><rect x="252" y="107.4" width="12" height="58.8" fill="#1d3fe3"/>
      <rect x="288" y="202" width="12" height="23" fill="#9aa8f5"/><rect x="288" y="180.9" width="12" height="21" fill="#0a1a7a"/><rect x="288" y="92.7" width="12" height="88.2" fill="#1d3fe3"/>
      <rect x="324" y="210.3" width="12" height="14.7" fill="#9aa8f5"/><rect x="324" y="195.6" width="12" height="14.7" fill="#0a1a7a"/><rect x="324" y="151.5" width="12" height="44.1" fill="#1d3fe3"/>
      <rect x="360" y="185" width="12" height="40" fill="#9aa8f5"/><rect x="360" y="122.1" width="12" height="62.9" fill="#0a1a7a"/>
      <rect x="396" y="195.6" width="12" height="29.4" fill="#9aa8f5"/><rect x="396" y="166.2" width="12" height="29.4" fill="#0a1a7a"/><rect x="396" y="107.4" width="12" height="58.8" fill="#1d3fe3"/>
      <rect x="432" y="210.3" width="12" height="14.7" fill="#9aa8f5"/><rect x="432" y="195.6" width="12" height="14.7" fill="#0a1a7a"/><rect x="432" y="166.2" width="12" height="29.4" fill="#1d3fe3"/>
    </g>
    <g font-size="3.2" fill="#333" text-anchor="middle">
      <text x="42" y="234">JAN</text><text x="78" y="234">FEB</text><text x="114" y="234">MAR</text><text x="150" y="234">APR</text><text x="186" y="234">MAY</text><text x="222" y="234">JUN</text><text x="258" y="234">JUL</text><text x="294" y="234">AUG</text><text x="330" y="234">SEP</text><text x="366" y="234">OCT</text><text x="402" y="234">NOV</text><text x="438" y="234">DEC</text>
    </g>
    <circle cx="360" cy="70" r="2" fill="#9aa8f5"/><text x="364" y="71.5" font-size="4" fill="#333">Receipts</text>
    <circle cx="393" cy="70" r="2" fill="#1d3fe3"/><text x="397" y="71.5" font-size="4" fill="#333">Sales</text>
    <circle cx="418" cy="70" r="2" fill="#0a1a7a"/><text x="422" y="71.5" font-size="4" fill="#333">Orders</text>
  </svg>
  <div class="footer"></div>
</section>

<section class="slide" style="left:375px;top:802px">
  <div class="process-title">PROCESS<small>INFOGRAPHIC</small></div>
  <svg class="abs" style="left:0;top:0" width="482" height="271" viewBox="0 0 482 271" font-family="Poppins, sans-serif">
    <defs>
      <marker id="arrowhead" markerWidth="5" markerHeight="5" refX="2.5" refY="2.5" orient="auto"><path d="M0 0L5 2.5L0 5z" fill="#0a1a7a"/></marker>
    </defs>
    <path d="M66 121h85a8 8 0 0 1 0 16a8 8 0 0 1 0 16h-85a6 6 0 0 0 0-16a6 6 0 0 0 0-16z" fill="#0a1a7a"/>
    <path d="M151 121h85a8 8 0 0 1 0 16a8 8 0 0 1 0 16h-85a8 8 0 0 0 0-32z" fill="#1d3fe3"/>
    <path d="M236 121h85a8 8 0 0 1 0 16a8 8 0 0 1 0 16h-85a8 8 0 0 0 0-32z" fill="#0a1a7a"/>
    <path d="M321 121h85a8 8 0 0 1 0 32h-85a8 8 0 0 0 0-32z" fill="#1d3fe3"/>
    <g font-size="14" font-weight="500" fill="#fff" text-anchor="middle">
      <text x="103" y="143">01</text><text x="189" y="143">02</text><text x="274" y="143">03</text><text x="358" y="143">04</text>
    </g>
    <g fill="none" stroke-width="2.2" marker-end="url(#arrowhead)">
      <path d="M134 119a21 21 0 0 1 40 -1" stroke="#0a1a7a"/>
      <path d="M219 119a21 21 0 0 1 40 -1" stroke="#1d3fe3"/>
      <path d="M304 119a21 21 0 0 1 40 -1" stroke="#0a1a7a"/>
    </g>
  </svg>
  <div class="step-label" style="left:68px;top:163px"><b>LOREM IPSUM</b><span>Lorem ipsum dolor sit amet consectetur adipiscing elit. Duis elit sapien.</span></div>
  <div class="step-label" style="left:154px;top:163px"><b>LOREM IPSUM</b><span>Lorem ipsum dolor sit amet consectetur adipiscing elit. Duis elit sapien.</span></div>
  <div class="step-label" style="left:239px;top:163px"><b>LOREM IPSUM</b><span>Lorem ipsum dolor sit amet consectetur adipiscing elit. Duis elit sapien.</span></div>
  <div class="step-label" style="left:324px;top:163px"><b>LOREM IPSUM</b><span>Lorem ipsum dolor sit amet consectetur adipiscing elit. Duis elit sapien.</span></div>
  <div class="footer"></div>
</section>

<section class="slide" style="left:679px;top:802px">
  <div class="process-title">PROCESS<small>INFOGRAPHIC</small></div>
  <svg class="abs" style="left:0;top:0" width="482" height="271" viewBox="0 0 482 271" font-family="Poppins, sans-serif">
    <g fill="#eeeff1"><rect x="69" y="140" width="64" height="90"/><rect x="162" y="140" width="64" height="90"/><rect x="255" y="140" width="64" height="90"/><rect x="348" y="140" width="64" height="90"/></g>
    <path d="M109 108v-12h44v12M201 108v-12h45v12M295 108v-12h44v12" fill="none" stroke="#9fe0d8" stroke-width="1"/>
    <g stroke-width="3" stroke="#fff">
      <polygon points="82,141 92,108 110,104 128,108 138,141 128,172 92,172" fill="#1d3fe3" transform="translate(0 -2)"/>
      <polygon points="175,141 185,108 203,104 221,108 231,141 221,172 185,172" fill="#0a1a7a" transform="translate(-1 -2)"/>
      <polygon points="268,141 278,108 296,104 314,108 324,141 314,172 278,172" fill="#1d3fe3" transform="translate(-1 -2)"/>
      <polygon points="361,141 371,108 389,104 407,108 417,141 407,172 371,172" fill="#0a1a7a" transform="translate(-2 -2)"/>
    </g>
    <g font-size="19" font-weight="500" fill="#fff" text-anchor="middle">
      <text x="101" y="146">01</text><text x="195" y="146">02</text><text x="288" y="146">03</text><text x="381" y="146">04</text>
    </g>
  </svg>
  <div class="step-label" style="left:66px;top:187px"><b>LOREM IPSUM</b><span>Lorem ipsum dolor sit amet consectetur adipiscing elit. Duis elit sapien.</span></div>
  <div class="step-label" style="left:159px;top:187px"><b>LOREM IPSUM</b><span>Lorem ipsum dolor sit amet consectetur adipiscing elit. Duis elit sapien.</span></div>
  <div class="step-label" style="left:252px;top:187px"><b>LOREM IPSUM</b><span>Lorem ipsum dolor sit amet consectetur adipiscing elit. Duis elit sapien.</span></div>
  <div class="step-label" style="left:345px;top:187px"><b>LOREM IPSUM</b><span>Lorem ipsum dolor sit amet consectetur adipiscing elit. Duis elit sapien.</span></div>
  <div class="footer"></div>
</section>

<!-- Row 6: section dividers -->
<section class="slide" style="left:72px;top:985px;background:var(--blue)">
  <div class="fill" role="img" aria-label="Soft blue gradient of overlapping wafer outlines" style="background:radial-gradient(ellipse 40% 90% at 30% 30%,#2a4af0 0%,transparent 70%),radial-gradient(ellipse 40% 90% at 75% 40%,#1a38d8 0%,transparent 70%),linear-gradient(135deg,#1f3fe0 0%,#1634c8 100%)"></div>
  <span class="centre-mark" style="top:75px;background:var(--white)"></span>
  <h2 class="centre-title" style="top:128px;color:var(--white)">Section<br>Slide</h2>
</section>

<section class="slide" style="left:375px;top:985px;background:var(--dark)">
  <div class="fill" role="img" aria-label="Dark photo of a silicon wafer on an inspection stage" style="background:radial-gradient(ellipse 55% 55% at 50% 60%,#2c3f48 0%,#17222c 55%,#080c14 100%)"></div>
  <span class="centre-mark" style="top:75px;background:var(--white)"></span>
  <h2 class="centre-title" style="top:128px;color:var(--white)">Section<br>Slide</h2>
</section>

<section class="slide" style="left:679px;top:985px;background:#c9d4e2">
  <div class="fill" role="img" aria-label="Bright photo of a silicon wafer on an inspection stage, pale blue tones" style="background:radial-gradient(ellipse 55% 55% at 55% 45%,#dfeffa 0%,#b4cde0 50%,#8fa2b8 100%)"></div>
  <span class="centre-mark" style="top:75px;background:var(--blue)"></span>
  <h2 class="centre-title" style="top:128px;color:var(--ink)">Section<br>Slide</h2>
</section>

</body>
</html>
```